Luxury packaging graphic design for a new Hair care elixir

We need a packaging design for a new product for our line extension of hair colouring. We have already a packaging that is very well received (all in pink) including all accesories and transport box (attached files).
For a new product - protein for the hair - we need a different design tapping into luxury segment.

Target Market(s)

This product is mainly for women between 25-65 that are looking forward to improve hair strukture and make hair looks better, nicer, softer, healthier. The product in the packaging could be used up to 2x times.

Industry/Entity Type

Hair And Beauty

Font styles to use
Serif
Sans Serif

Colors

Designer to choose colors to be used in the design.

Requirements
Must have
• The material of the packaging are carton/styropor/and glass (attached a picture of packaging design to be adapted). The components are quite small so the packaging plays a big role to increase the value of what it is inside. The packaging needs to be inline with our actual packaging designs and corporate identity as they may be delivered together so as an assamble it should look nice, beautiful and of high quality.
• The graphic design for the different components to be adapted are:
• - grapich design for outside box
• - graphic design for the inside bottles
• - graphic design for the flyer/instructions inside the box
Nice to have
• It needs to feel that the packaging is Wow! It is going to be delivered per post so there have to be a beautiful opening effect. Eventually to work with colours like black, white and gold would give a nice luxury feeling.
• The actual product inside is a concentrated protein component so it is very small, therefore the packaging should show that even if small it is an elixir for the hair.
Should not have
• a totally diffenet look as our actual designs.

```html
<!DOCTYPE html>
<html lang="en">
<head>
<meta charset="UTF-8">
<title>Nora Vey – Hair Elixier Label</title>
<link rel="stylesheet" href="https://fonts.googleapis.com/css2?family=Montserrat:wght@700&family=Raleway:wght@200;300&display=swap">
<style>
  :root {
    --paper: #ffffff;
    --ink: #000000;
    --gold: #c9a24a;
    --gold-deep: #7a5a1e;
    --gold-soft: #e2c47a;
    --white: #ffffff;
  }
  html, body {
    margin: 0;
    padding: 0;
    width: 1200px;
    height: 2327px;
    overflow: hidden;
    background: var(--paper);
  }
  .canvas {
    position: relative;
    width: 1200px;
    height: 2327px;
    background: var(--paper);
  }
  .label {
    position: absolute;
    left: 85px;
    top: 34px;
    width: 1077px;
    height: 2178px;
    background: var(--ink);
  }
  .hair-waves {
    position: absolute;
    left: 34px;
    top: 30px;
    right: 30px;
    bottom: 30px;
    background:
      radial-gradient(ellipse at 20% 30%, rgba(226,196,122,0.55), transparent 45%),
      radial-gradient(ellipse at 80% 55%, rgba(201,162,74,0.5), transparent 50%),
      radial-gradient(ellipse at 35% 85%, rgba(226,196,122,0.45), transparent 45%),
      linear-gradient(160deg, #2a1f0a 0%, var(--gold-deep) 35%, #1a1306 55%, var(--gold-deep) 80%, #140f05 100%);
  }
  .title-panel {
    position: absolute;
    left: 163px;
    top: 316px;
    width: 777px;
    height: 718px;
    background: var(--ink);
    text-align: center;
  }
  .brand-name {
    margin: 96px 0 0;
    font-family: "Montserrat", sans-serif;
    font-weight: 700;
    font-size: 128px;
    line-height: 1;
    letter-spacing: 1px;
    color: var(--white);
  }
  .tagline {
    margin: 34px 0 0;
    font-family: "Montserrat", sans-serif;
    font-weight: 700;
    font-size: 42px;
    letter-spacing: 1px;
    color: var(--white);
  }
  .product-name {
    margin: 150px 0 0;
    font-family: "Raleway", sans-serif;
    font-weight: 200;
    font-size: 78px;
    letter-spacing: 4px;
    color: var(--gold);
  }
  .product-type {
    margin: 14px 0 0;
    font-family: "Raleway", sans-serif;
    font-weight: 300;
    font-size: 36px;
    letter-spacing: 1px;
    color: var(--gold);
  }
  .volume {
    position: absolute;
    left: 0;
    right: 0;
    bottom: 64px;
    margin: 0;
    text-align: center;
    font-family: "Raleway", sans-serif;
    font-weight: 300;
    font-size: 38px;
    color: var(--gold-soft);
  }
</style>
</head>
<body>
<div class="canvas">
  <div class="label">
    <div class="hair-waves" role="img" aria-label="Flowing gold line pattern of wavy hair strands on black"></div>
    <div class="title-panel">
      <h1 class="brand-name">nora vey</h1>
      <p class="tagline">YOUR SHADE, YOUR WAY</p>
      <h2 class="product-name">HAIR ELIXIER</h2>
      <p class="product-type">Concentrated Serum</p>
    </div>
    <p class="volume">60ml ℮</p>
  </div>
</div>
</body>
</html>
```